We are growing our coaching practice and need some help creating collateral

Our organisation is building a coaching practice. It's going well and we want to take it to the next level. To date, we've done our own basic marketing material (attached), but now we want to create something more substantial that captures our approach and gives us confidence and pride when talking to customers. Things to note - we aren't looking for logo design, that's a separate branding discussion in our organisation. We are looking for someone to take our existing content and make it look good - this might be in the form of a flyer or PPT slide deck for example.
The format we are looking for is the offering title - in this case, 'Coaching', a brief description, and then some further detail.
Target Market(s)
Corporate, Healthcare, IT
Colors
Designer to choose colors to be used in the design.
Look and feel

```html
<!DOCTYPE html>
<html lang="en">
<head>
<meta charset="utf-8">
<title>BW Executive Coaching</title>
<link href="https://fonts.googleapis.com/css2?family=Raleway:wght@300;400;500;600;800&display=swap" rel="stylesheet">
<style>
  :root {
    --orange: #f28a30;
    --orange-deep: #ec7a22;
    --ink: #3d3f42;
    --text: #3a3a3a;
    --disc: #efeff0;
    --bar: #4a4b4e;
    --white: #ffffff;
  }
  * { margin: 0; padding: 0; box-sizing: border-box; }
  html, body { width: 850px; height: 1200px; overflow: hidden; background: var(--white); }
  .flyer {
    position: relative; width: 850px; height: 1200px; overflow: hidden;
    font-family: "Raleway", sans-serif; color: var(--text); background: var(--white);
  }
  .art { position: absolute; left: 0; top: 0; width: 850px; height: 620px; }
  .brand-name {
    position: absolute; left: 42px; top: 146px;
    font-size: 30px; font-weight: 400; color: var(--ink); letter-spacing: 1px;
  }
  .title { position: absolute; left: 560px; top: 384px; width: 290px; text-align: center; }
  .title-line {
    display: flex; align-items: center; justify-content: center; gap: 6px;
    color: var(--orange); font-size: 33px; font-weight: 400;
  }
  .title-line::before, .title-line::after { content: ""; height: 2px; background: var(--orange); width: 70px; }
  .title-line.lower::before, .title-line.lower::after { width: 26px; }
  .title-main { font-size: 41px; font-weight: 800; color: var(--ink); line-height: 1.15; margin: 2px 0; }
  .intro { position: absolute; left: 33px; font-size: 17.4px; font-weight: 300; line-height: 24px; }
  .intro.first { top: 318px; width: 360px; }
  .intro.second { top: 452px; width: 520px; }
  .body-copy {
    position: absolute; left: 37px; width: 805px; font-size: 20.3px; font-weight: 300; line-height: 24.5px;
  }
  .body-copy.systems { top: 603px; }
  .body-copy.leaders { top: 727px; }
  .rule { position: absolute; left: 240px; top: 713px; width: 359px; height: 1px; background: var(--ink); }
  .offer {
    position: absolute; left: 31px; top: 856px; width: 806px; height: 256px;
    background: var(--orange); color: var(--white);
    padding: 10px 10px 0 10px; font-size: 19px; font-weight: 400; line-height: 27.2px; letter-spacing: 1.5px;
  }
  .offer-band { background: var(--orange-deep); margin: -10px -10px 0; padding: 10px 10px 0; }
  .contact {
    position: absolute; left: 60px; top: 1146px; width: 748px; height: 54px;
    background: var(--bar); color: var(--white);
    font-size: 31px; font-weight: 600; text-align: center; line-height: 54px;
  }
</style>
</head>
<body>
<main class="flyer">
  <svg class="art" viewBox="0 0 850 620">
    <defs>
      <clipPath id="photo-clip"><circle cx="720" cy="112" r="344"/></clipPath>
      <linearGradient id="scene-tone" x1="0" y1="0" x2="0" y2="1">
        <stop offset="0" stop-color="#4f7a3c"/>
        <stop offset="0.45" stop-color="#8a6a3e"/>
        <stop offset="0.7" stop-color="#7d8a84"/>
        <stop offset="1" stop-color="#a9b3b4"/>
      </linearGradient>
    </defs>
    <circle cx="720" cy="112" r="368" fill="none" stroke="var(--orange)" stroke-width="9"
            stroke-dasharray="560 2000" transform="rotate(118 720 112)"/>
    <circle cx="720" cy="112" r="356" fill="none" stroke="var(--orange)" stroke-width="3"
            stroke-dasharray="600 2000" transform="rotate(115 720 112)"/>
    <rect class="photo" role="img" aria-label="Wooden truss footbridge over a river with forest behind"
          x="360" y="0" width="490" height="460" fill="url(#scene-tone)" clip-path="url(#photo-clip)"/>
    <circle cx="702" cy="458" r="148" fill="var(--disc)"/>
    <g stroke="var(--orange)" stroke-width="3">
      <line x1="24" y1="16" x2="80" y2="96"/>
      <line x1="14" y1="222" x2="74" y2="298"/>
      <line x1="178" y1="227" x2="238" y2="304"/>
    </g>
  </svg>

  <div class="brand-name">bridgewell</div>

  <div class="title">
    <div class="title-line">BW</div>
    <div class="title-main">EXECUTIVE</div>
    <div class="title-line lower">COACHING</div>
  </div>

  <p class="intro first">We believe great coaching is a bridge: one that enables you to see more clearly and cross the unexpected chasms; one that supports and challenges your thinking and actions to progress your significant goals.</p>
  <p class="intro second">We build a creative and confidential partnership with you, one that is grounded in the science of leadership, change and coaching psychology so that practical results are<br>an expectation and not left to chance.</p>

  <p class="body-copy systems">Our coaches are highly attuned to the human systems within which you work and live, since understanding those interconnected forces is vital to unlock movement. We build on your existing strengths and seek sustainable shifts, ones that create ripple effects of positive change.</p>
  <div class="rule"></div>
  <p class="body-copy leaders">Leaders everywhere face unprecedented change, pressure, ambiguity, culture and accountability dilemmas. And yet every leader also has a different story, different terrain to navigate and different aspirations. This is where executive coaching with Bridgewell can create extraordinary results.</p>

  <section class="offer">
    <div class="offer-band">Our coaching packages typically consist of blocks of 7 hourly sessions, conducted fortnightly (with flexibility to customise).<br>For EL2 leaders, the investment in a block of 7 sessions is $3400 + GST. This includes significant preparation and conceptualisation time before and after sessions by your coach to ensure you achieve maximum value.</div>
    Why not explore the possibilities executive coaching offers through a no obligation initial session, ensuring the approach and the coach is a good fit for you? Contact Dan Morrow,
  </section>

  <div class="contact">Ph. 0412 555 018, dan.morrow@bridgewell.com</div>
</main>
</body>
</html>
```